The Korvane LLC Asset Classes

I'm looking for for two designs here to go into powerpoint and potentially as a standalone PDF. My company does wealth management.
Graphic Image #1
I break down the investment world into 4 broad categories
-Preservation
-Capital Markets
-Real Estate
-Alternatives
In each broad category, there are subcategories:
Preservation: cash, checking/savings accounts, money market accounts, CD's, and fixed annuities.
Capital Markets: Publicly traded stocks and bonds
Real Estate: single-family residence, retail, industrial, multifamily, and office
Alternatives: private equity, private credit, cryptocurrency, asset-backed loans, tax liens, oil & gas, litigation finance, and royalties
Graphic 2: Please see the bottom f page 1 of the Tessolin Decks PDF.
Just like in graphic one, you have 4 categories of the Capital Markets and their respective subcategories
Category 1: Domestic Stocks: Subcategories are Large, mid, and small size companies
Category 2: International Stocks: Subcategories are Large, Mid/Small and by region - Developed and Emerging
Category 3: Fixed Income: You have subcategories like corporate, municipal, government, domestic, international
Category 4: Alternatives: The subcategories are metals and real estate
---------------------
I'm looking to create a graphic (either pie chart, or a circle broken into parts or some other clever way to illustrate this) to clearly illustrate both of these universes in a clean, professional, slick manner.
Target Market(s)
Investors
Colors
Designer to choose colors to be used in the design.
Requirements
Must have
- Clean
- professional
- Easy to read
- Creative
- Visually appealling
Nice to have
- I have attached my logo and some marketing materials so you can get a feel of what I am doing. Maybe you can clean this up too!

```html
<!DOCTYPE html>
<html lang="en">
<head>
<meta charset="utf-8">
<title>Korvane LLC – Investment World Categories</title>
<link href="https://fonts.googleapis.com/css2?family=Fira+Sans:wght@300;400;500;700&display=swap" rel="stylesheet">
<style>
  :root{
    --stage:#d9dadc;
    --paper:#ffffff;
    --orange:#ecae62;
    --orange-deep:#e69a55;
    --preservation:#00305f;
    --capital:#0a69ad;
    --realestate:#1aa3de;
    --alternatives:#74c0e0;
    --brand:#17689f;
    --ink-light:#ffffff;
  }
  *{box-sizing:border-box;margin:0;padding:0}
  html,body{width:1200px;height:1000px;overflow:hidden}
  body{background:var(--stage);font-family:"Fira Sans",sans-serif;position:relative}

  .slide{position:absolute;left:0;top:162px;width:1200px;height:675px;background:var(--paper);overflow:hidden}

  .brand{position:absolute;left:72px;top:100px;display:flex;align-items:center;gap:12px}
  .brand-dot{width:40px;height:40px;border-radius:50%;background:var(--brand)}
  .brand-name{font-size:34px;font-weight:500;color:var(--brand);letter-spacing:.2px}

  .title-card{position:absolute;left:74px;top:223px;width:312px;height:373px;background:var(--orange);padding:32px 0 0 36px}
  .title-card h1{font-weight:300;font-size:45px;line-height:54px;color:var(--ink-light);letter-spacing:.3px}

  .chain{position:absolute;left:0;top:0;width:1200px;height:675px;pointer-events:none}
  .chain .arc-label{font-family:"Fira Sans",sans-serif;font-weight:700;font-size:13px;fill:#fff;letter-spacing:.6px}

  .column{position:absolute;top:220px;width:94px;height:377px;color:var(--ink-light);
    display:flex;flex-direction:column;align-items:center;justify-content:space-evenly;
    text-align:center;font-size:12px;font-weight:500;line-height:15px;
    border-top:4px solid var(--orange-deep);box-shadow:-14px 20px 22px rgba(40,50,80,.12)}
  .column::before{content:"";position:absolute;top:-10px;left:50%;transform:translateX(-50%);
    border-left:8px solid transparent;border-right:8px solid transparent;border-bottom:7px solid var(--orange-deep)}
  .column .divider{width:54px;height:1px;background:rgba(255,255,255,.9);flex:none}
  .column--preservation{left:532px;background:var(--preservation)}
  .column--capital{left:689px;background:var(--capital);justify-content:center}
  .column--realestate{left:844px;background:var(--realestate)}
  .column--alternatives{left:1001px;background:var(--alternatives)}
</style>
</head>
<body>
<main class="slide">
  <div class="brand">
    <span class="brand-dot"></span>
    <span class="brand-name">Korvane LLC</span>
  </div>

  <section class="title-card">
    <h1>Investment World Categories</h1>
  </section>

  <svg class="chain" viewBox="0 0 1200 675" aria-hidden="true">
    <defs>
      <linearGradient id="link-a" gradientUnits="userSpaceOnUse" x1="581" x2="736" y1="0" y2="0">
        <stop offset="0" stop-color="#00305f"/><stop offset="1" stop-color="#0a69ad"/>
      </linearGradient>
      <linearGradient id="link-b" gradientUnits="userSpaceOnUse" x1="736" x2="891" y1="0" y2="0">
        <stop offset="0" stop-color="#0a69ad"/><stop offset="1" stop-color="#1aa3de"/>
      </linearGradient>
      <linearGradient id="link-c" gradientUnits="userSpaceOnUse" x1="891" x2="1047" y1="0" y2="0">
        <stop offset="0" stop-color="#1aa3de"/><stop offset="1" stop-color="#74c0e0"/>
      </linearGradient>
      <filter id="soft" x="-30%" y="-30%" width="160%" height="160%">
        <feDropShadow dx="-4" dy="8" stdDeviation="6" flood-color="#1c2a44" flood-opacity=".22"/>
      </filter>
      <path id="arc-1" d="M539,129 A42,42 0 0 1 623,129"/>
      <path id="arc-2" d="M694,129 A42,42 0 0 1 778,129"/>
      <path id="arc-3" d="M849,129 A42,42 0 0 1 933,129"/>
      <path id="arc-4" d="M1005,129 A42,42 0 0 1 1089,129"/>
    </defs>

    <g class="links" filter="url(#soft)">
      <path d="M581,72 Q658,132 736,72 L736,186 Q658,126 581,186 Z" fill="url(#link-a)"/>
      <path d="M736,72 Q813,132 891,72 L891,186 Q813,126 736,186 Z" fill="url(#link-b)"/>
      <path d="M891,72 Q969,132 1047,72 L1047,186 Q969,126 891,186 Z" fill="url(#link-c)"/>
      <circle cx="581" cy="129" r="57" fill="var(--preservation)"/>
      <circle cx="736" cy="129" r="57" fill="var(--capital)"/>
      <circle cx="891" cy="129" r="57" fill="var(--realestate)"/>
      <circle cx="1047" cy="129" r="57" fill="var(--alternatives)"/>
    </g>

    <g class="hubs" filter="url(#soft)" fill="#fff">
      <circle cx="581" cy="129" r="34"/>
      <circle cx="736" cy="129" r="34"/>
      <circle cx="891" cy="129" r="34"/>
      <circle cx="1047" cy="129" r="34"/>
    </g>

    <text class="arc-label"><textPath href="#arc-1" startOffset="50%" text-anchor="middle">Preservation</textPath></text>
    <text class="arc-label"><textPath href="#arc-2" startOffset="50%" text-anchor="middle">Capital Markets</textPath></text>
    <text class="arc-label"><textPath href="#arc-3" startOffset="50%" text-anchor="middle">Real Estate</textPath></text>
    <text class="arc-label"><textPath href="#arc-4" startOffset="50%" text-anchor="middle">Alternatives</textPath></text>

    <g class="icon icon--preservation" fill="var(--preservation)">
      <circle cx="582" cy="124" r="10"/>
      <text x="582" y="129" text-anchor="middle" font-family="Fira Sans, sans-serif" font-weight="700" font-size="13" fill="#fff">$</text>
      <rect x="577" y="106" width="2" height="5"/><rect x="581" y="104" width="2" height="7"/><rect x="585" y="106" width="2" height="5"/>
      <rect x="564" y="138" width="5" height="10"/>
      <path d="M570,140 L584,140 Q590,140 597,135 L599,138 Q590,147 580,147 L570,147 Z"/>
    </g>

    <g class="icon icon--capital" fill="var(--capital)">
      <rect x="722" y="130" width="4" height="14"/><rect x="728" y="126" width="4" height="18"/>
      <rect x="734" y="129" width="4" height="15"/><rect x="740" y="123" width="4" height="21"/>
      <rect x="746" y="118" width="4" height="26"/>
      <path d="M720,124 L730,116 L737,121 L748,111" stroke="var(--capital)" stroke-width="2.5" fill="none"/>
      <path d="M743,110 L750,109 L749,116 Z"/>
    </g>

    <g class="icon icon--realestate" fill="var(--realestate)">
      <path d="M872,128 L891,114 L910,128 Z"/>
      <rect x="875" y="129" width="32" height="14"/>
      <rect x="887" y="134" width="8" height="9" fill="#fff"/>
      <rect x="878" y="132" width="5" height="5" fill="#fff"/><rect x="899" y="132" width="5" height="5" fill="#fff"/>
    </g>

    <g class="icon icon--alternatives" stroke="var(--alternatives)" stroke-width="2" fill="var(--alternatives)">
      <line x1="1047" y1="129" x2="1035" y2="117"/><line x1="1047" y1="129" x2="1061" y2="121"/>
      <line x1="1047" y1="129" x2="1037" y2="143"/><line x1="1047" y1="129" x2="1058" y2="141"/>
      <line x1="1035" y1="117" x2="1049" y2="112"/><line x1="1049" y1="112" x2="1061" y2="121"/>
      <circle cx="1047" cy="129" r="5"/><circle cx="1035" cy="117" r="3.5"/>
      <circle cx="1061" cy="121" r="3.5"/><circle cx="1037" cy="143" r="3.5"/>
      <circle cx="1058" cy="141" r="3.5"/><circle cx="1049" cy="112" r="3"/>
    </g>
  </svg>

  <ul class="column column--preservation" style="list-style:none">
    <li>Cash</li><li class="divider"></li>
    <li>Checking/<br>Savings<br>Accounts</li><li class="divider"></li>
    <li>Money<br>Market<br>Accounts</li><li class="divider"></li>
    <li>CD’s</li><li class="divider"></li>
    <li>Fixed<br>Annuities</li>
  </ul>

  <ul class="column column--capital" style="list-style:none">
    <li>Publicly<br>Traded<br>Stocks and<br>Bonds</li>
  </ul>

  <ul class="column column--realestate" style="list-style:none">
    <li>Single-family<br>Residence</li><li class="divider"></li>
    <li>Retail</li><li class="divider"></li>
    <li>Industrial</li><li class="divider"></li>
    <li>Multifamily</li><li class="divider"></li>
    <li>Office</li>
  </ul>

  <ul class="column column--alternatives" style="list-style:none">
    <li>Private Equity</li><li class="divider"></li>
    <li>Private Credit</li><li class="divider"></li>
    <li>Cryptocurrency</li><li class="divider"></li>
    <li>Asset-backed<br>Loans</li><li class="divider"></li>
    <li>Tax Liens</li><li class="divider"></li>
    <li>Oil &amp; Gas</li><li class="divider"></li>
    <li>Litigation<br>Finance</li><li class="divider"></li>
    <li>Royalties</li>
  </ul>
</main>
</body>
</html>
```